Colin Vardek Business card

Hey there, I’m hoping to have a business card designed. I’m in Real estate and just switched to a new Brokerage called: The Harbourline Property Group

The back could just be the company name maybe or whatever looks good!

I’ve attached some logos of our company and some cards my buddy had done up.

On the card:
Colin Vardek
colinvardek@mailora.com
587-412-9065
colinvardek.ca

Target Market(s)

Home buyers and sellers

Industry/Entity Type

Real Estate

Contact Information for Business Card

just looking for a cool and modern design with my picture on it. I like the idea of Black and red being used.

Requirements
Must have
• all the details provided. I'm open to anything. Just want a professional looking card.

```html
<!DOCTYPE html>
<html lang="en">
<head>
<meta charset="utf-8">
<title>Colin Vardek – Business Card</title>
<link rel="stylesheet" href="https://fonts.googleapis.com/css2?family=Montserrat:wght@500;600;800&display=swap">
<style>
  :root {
    --bg: #e7e5e6;
    --card: #232227;
    --red: #c8203a;
    --white: #ffffff;
    --emboss: #2f2e35;
    --photo-a: #3a3238;
    --photo-b: #1f1e23;
  }
  * { box-sizing: border-box; margin: 0; padding: 0; }
  html, body { width: 1200px; height: 852px; overflow: hidden; }
  body {
    background: var(--bg);
    font-family: "Montserrat", sans-serif;
    position: relative;
  }
  .card {
    position: absolute;
    left: 337px;
    width: 525px;
    height: 300px;
    border-radius: 22px;
    background: var(--card);
    box-shadow: 0 0 0 3px var(--red), 0 14px 30px rgba(0,0,0,.25);
    overflow: hidden;
  }
  .card--back { top: 84px; }
  .card--front { top: 466px; }

  .back-name {
    position: absolute;
    inset: 0;
    display: flex;
    flex-direction: column;
    align-items: center;
    justify-content: center;
    color: var(--emboss);
    font-weight: 800;
    text-transform: uppercase;
    text-align: center;
    line-height: 1;
  }
  .back-name .line-sm { font-size: 22px; letter-spacing: 2px; }
  .back-name .line-lg { font-size: 44px; letter-spacing: 1px; margin-top: 6px; }

  .brand {
    position: absolute;
    left: 40px;
    top: 74px;
    width: 270px;
    z-index: 2;
    color: var(--white);
    font-weight: 800;
    text-transform: uppercase;
    line-height: 1;
  }
  .brand .line-sm { display: block; font-size: 15px; letter-spacing: 1.5px; }
  .brand .line-lg { display: block; font-size: 25px; margin-top: 6px; white-space: nowrap; }

  .photo {
    position: absolute;
    right: 0;
    top: 18px;
    width: 195px;
    height: 182px;
    z-index: 1;
    background: radial-gradient(ellipse at 50% 35%, var(--photo-a), var(--photo-b) 75%);
  }

  .band {
    position: absolute;
    left: 150px;
    top: 198px;
    width: 375px;
    height: 66px;
    z-index: 2;
    background: var(--red);
    clip-path: polygon(0 0, 100% 0, 100% 100%, 14px 100%, 0 72%);
  }
  .agent-name {
    position: absolute;
    right: 30px;
    top: 12px;
    color: var(--white);
    font-weight: 600;
    font-size: 17px;
    white-space: nowrap;
  }
  .contacts {
    position: absolute;
    left: 28px;
    top: 7px;
    list-style: none;
    color: var(--white);
    font-weight: 500;
    font-size: 11.5px;
    line-height: 17px;
    white-space: nowrap;
  }
  .contacts li { display: flex; align-items: center; gap: 6px; }
  .contacts svg { width: 11px; height: 11px; flex: none; }
</style>
</head>
<body>
  <section class="card card--back" aria-label="Card back">
    <div class="back-name">
      <span class="line-sm">The Harbourline</span>
      <span class="line-lg">Property Group</span>
    </div>
  </section>

  <section class="card card--front" aria-label="Card front">
    <div class="brand">
      <span class="line-sm">The Harbourline</span>
      <span class="line-lg">Property Group</span>
    </div>

    <div class="photo" role="img" aria-label="Portrait photo of Colin Vardek in a dark blazer and white shirt"></div>

    <div class="band">
      <ul class="contacts">
        <li>
          <svg viewBox="0 0 12 12" aria-hidden="true"><path fill="#fff" d="M2.5 1h2l1 2.5-1.3 1a6 6 0 0 0 3.3 3.3l1-1.3L11 7.5v2A1.5 1.5 0 0 1 9.5 11 8.5 8.5 0 0 1 1 2.5 1.5 1.5 0 0 1 2.5 1z"/></svg>
          587-412-9065
        </li>
        <li>
          <svg viewBox="0 0 12 12" aria-hidden="true"><rect x="1" y="2.5" width="10" height="7" rx="1" fill="#fff"/><path d="M1.5 3l4.5 3.5L10.5 3" fill="none" stroke="#c8203a" stroke-width="1"/></svg>
          colinvardek@mailora.com
        </li>
        <li>
          <svg viewBox="0 0 12 12" aria-hidden="true"><circle cx="6" cy="6" r="5" fill="none" stroke="#fff" stroke-width="1.2"/><ellipse cx="6" cy="6" rx="2" ry="5" fill="none" stroke="#fff" stroke-width="1"/><path d="M1 6h10" stroke="#fff" stroke-width="1"/></svg>
          colinvardek.ca
        </li>
      </ul>
      <p class="agent-name">Colin Vardek</p>
    </div>
  </section>
</body>
</html>
```